Exciting & Elegant Stationary Pack

Stationary consists of
1. Letter head / Envelope
2. Business Card
3. Invoice
4. 40x40mm sticker

Attached files;

1. Logo (Other formats available on request)
2. MS word Doc - For information and description of design
3. Website image (This will be our new website so use the colours so everything ties together)
4. Sample of stationary pack we like, but feel free to be creative

Target Market(s)

Home improvement

Industry/Entity Type

Construction

Font styles to use
Other font styles liked:
• Leave up to designer - We like font used on (website attached image)

Requirements
Must have
• Please look at uploaded file of sample website and use colours
Nice to have
• Any type of business card design - eg. metal, die cut, embossed, etc...

```html
<!DOCTYPE html>
<html lang="en">
<head>
<meta charset="utf-8">
<title>Groutline Business Card</title>
<link rel="stylesheet" href="https://fonts.googleapis.com/css2?family=Arimo:wght@400;700&display=swap">
<style>
  :root {
    --orange: #f28a3c;
    --navy: #154a6e;
    --white: #ffffff;
    --backdrop: #e9e6e1;
  }
  * { margin: 0; padding: 0; box-sizing: border-box; }
  html, body { width: 1200px; height: 950px; overflow: hidden; }
  body {
    background: var(--backdrop);
    font-family: "Arimo", Arial, sans-serif;
    position: relative;
  }
  .card {
    position: absolute;
    width: 620px;
    height: 354px;
    overflow: hidden;
    box-shadow: 0 6px 18px rgba(0,0,0,0.18);
  }
  /* Front */
  .card-front { left: 70px; top: 60px; background: var(--orange); }
  .card-front .brand {
    position: absolute; left: 0; right: 0; top: 118px;
    text-align: center;
    font-size: 42px; font-weight: 700; letter-spacing: 1px;
    color: var(--navy);
  }
  .card-front .site {
    position: absolute; left: 0; right: 0; bottom: 44px;
    text-align: center;
    font-size: 15px; letter-spacing: 6px;
    color: var(--white);
  }
  /* Back */
  .card-back { left: 510px; top: 520px; background: var(--white); }
  .card-back .band { position: absolute; inset: 0; }
  .card-back .brand {
    position: absolute; right: 40px; top: 56px;
    font-size: 28px; font-weight: 700; letter-spacing: 1px;
    color: var(--white);
    white-space: nowrap;
  }
  .person { position: absolute; left: 40px; top: 168px; }
  .person .name { font-size: 19px; font-weight: 700; color: var(--navy); }
  .person .role { font-size: 14px; color: var(--orange); margin-top: 4px; }
  .licence {
    position: absolute; right: 34px; top: 194px;
    font-size: 14px; color: var(--white);
  }
  .contacts {
    position: absolute; left: 40px; bottom: 28px;
    list-style: none;
    color: var(--white); font-size: 14px;
  }
  .contacts li { display: flex; align-items: center; gap: 12px; height: 22px; }
  .contacts svg { width: 14px; height: 14px; flex: none; }
</style>
</head>
<body>

<section class="card card-front">
  <div class="brand">GROUTLINE</div>
  <div class="site">www.groutline.com.au</div>
</section>

<section class="card card-back">
  <svg class="band" viewBox="0 0 620 354" preserveAspectRatio="none" aria-hidden="true">
    <polygon points="380,0 620,0 620,354 0,354 0,238 300,238 350,128" fill="var(--navy)"/>
  </svg>
  <div class="brand">GROUTLINE</div>
  <div class="person">
    <div class="name">Mara Lindqvist</div>
    <div class="role">Project Manager</div>
  </div>
  <div class="licence">Lic No.,204519b</div>
  <ul class="contacts">
    <li>
      <svg viewBox="0 0 14 14" aria-hidden="true"><rect x="3" y="0.5" width="8" height="13" rx="1.5" fill="none" stroke="#fff" stroke-width="1.4"/><circle cx="7" cy="11" r="0.9" fill="#fff"/></svg>
      0400 317 552
    </li>
    <li>
      <svg viewBox="0 0 14 14" aria-hidden="true"><rect x="0.5" y="2.5" width="13" height="9" fill="#fff"/><polyline points="0.5,2.5 7,8 13.5,2.5" fill="none" stroke="var(--navy)" stroke-width="1.2"/></svg>
      info@groutline.com.au
    </li>
    <li>
      <svg viewBox="0 0 14 14" aria-hidden="true"><circle cx="7" cy="7" r="6.3" fill="#fff"/><circle cx="7" cy="7" r="2.6" fill="var(--navy)"/></svg>
      www.groutline.com.au
    </li>
  </ul>
</section>

</body>
</html>
```